Business card design for my company.
I would like the card's background colour to be black. You can also see our web site to get an idea of our brand. https://www.tmwhomecrafting.com.au/
- Name
- Email

```html
<!DOCTYPE html>
<html lang="en">
<head>
<meta charset="utf-8">
<title>TMW Home Crafting – Business Card</title>
<link rel="stylesheet" href="https://fonts.googleapis.com/css2?family=Montserrat:wght@400;500;700;800&display=swap">
<style>
  :root {
    --stage: #161616;
    --card: #1e1e1e;
    --card-back: #1a1a1a;
    --band: #262626;
    --pattern-a: #222222;
    --pattern-b: #2c2c2c;
    --green: #1f9a4a;
    --white: #f2f2f2;
    --muted: #d8d8d8;
  }
  * { box-sizing: border-box; margin: 0; padding: 0; }
  html, body {
    width: 1200px; height: 900px; overflow: hidden;
    background: var(--stage);
    font-family: "Montserrat", sans-serif;
  }
  .canvas { position: relative; width: 1200px; height: 900px; }
  .card {
    position: absolute; width: 540px; height: 309px;
    border-radius: 14px; overflow: hidden;
    box-shadow: 0 18px 40px rgba(0,0,0,.55);
  }
  /* Back */
  .card-back { left: 150px; top: 100px; background: var(--card-back); }
  .back-pattern {
    position: absolute; inset: 0;
    background: linear-gradient(120deg, var(--pattern-a) 0%, var(--pattern-b) 100%);
  }
  .back-brand {
    position: absolute; right: 36px; bottom: 120px;
    display: flex; align-items: center; gap: 8px;
    color: var(--white); font-weight: 700; font-size: 15px; letter-spacing: 1px;
  }
  .brand-mark { width: 10px; height: 10px; background: var(--green); }
  /* Front */
  .card-front { left: 510px; top: 470px; background: var(--card); }
  .front-band { position: absolute; inset: 0; }
  .front-brand {
    position: absolute; left: 34px; top: 128px;
    display: flex; align-items: center; gap: 10px;
    color: var(--white); font-weight: 800; font-size: 21px; letter-spacing: 1px; line-height: 1.1;
  }
  .front-brand .brand-mark { width: 14px; height: 14px; }
  .details { position: absolute; left: 290px; top: 62px; }
  .person-name { color: var(--green); font-weight: 800; font-size: 22px; letter-spacing: 1px; }
  .person-title { color: var(--white); font-size: 14px; margin-top: 2px; }
  .divider { width: 14px; height: 2px; background: var(--green); margin: 12px 0 10px; }
  .contact-list { list-style: none; }
  .contact-list li {
    display: flex; align-items: center; gap: 8px;
    color: var(--muted); font-size: 12.5px; margin-bottom: 8px;
  }
  .contact-list svg { width: 12px; height: 12px; flex: none; fill: var(--green); }
</style>
</head>
<body>
<main class="canvas">
  <section class="card card-back">
    <div class="back-pattern" role="img" aria-label="Tone-on-tone repeated brand pattern"></div>
    <div class="back-brand"><span class="brand-mark"></span>TMW HOME CRAFTING</div>
  </section>

  <section class="card card-front">
    <svg class="front-band" viewBox="0 0 540 309" preserveAspectRatio="none" aria-hidden="true">
      <polygon points="0,309 400,110 540,150 540,309" fill="var(--band)"/>
    </svg>
    <div class="front-brand"><span class="brand-mark"></span><span>TMW HOME<br>CRAFTING</span></div>
    <div class="details">
      <h1 class="person-name">DARREN HOLT</h1>
      <p class="person-title">CEO/Founder</p>
      <div class="divider"></div>
      <ul class="contact-list">
        <li><svg viewBox="0 0 24 24"><path d="M6.6 10.8a15 15 0 0 0 6.6 6.6l2.2-2.2c.3-.3.7-.4 1-.2 1.1.4 2.3.6 3.6.6.6 0 1 .4 1 1V20c0 .6-.4 1-1 1A17 17 0 0 1 3 4c0-.6.4-1 1-1h3.5c.6 0 1 .4 1 1 0 1.3.2 2.5.6 3.6.1.3 0 .7-.2 1z"/></svg>555-214-7093</li>
        <li><svg viewBox="0 0 24 24"><path d="M2 5h20v14H2z M2 5l10 8 10-8" stroke="var(--card)" stroke-width="1.5"/></svg>info@tmwhomecrafting.com.au</li>
        <li><svg viewBox="0 0 24 24"><circle cx="12" cy="12" r="10"/><path d="M2 12h20M12 2c3 3 3 17 0 20M12 2c-3 3-3 17 0 20" stroke="var(--card)" stroke-width="1.3" fill="none"/></svg>www.tmwhomecrafting.com.au</li>
      </ul>
    </div>
  </section>
</main>
</body>
</html>
```